Business card design for Virtual Assistance company

I need a business card designed for my virtual assistance company. We are a small company who services primarily C-level executive clients. The card needs to be double sided with the following contact information on the back:
Melissa Thornbury
Owner/CEO
info@rkpadvisory.net
www.rkpadvisory.net
555.302.9817

The front side should just have the company name incorporated: "RKP Advisory" and "virtual assistance"

The card should be simplistic, but eye catching and should speak to high level executives. Our primary focus areas consist of executive assistance and government contracting.

Target Market(s)

CEOs and executives

Contact Information for Business Card

see project description. phone, email, website.

Colors

Designer to choose only greyscale colors for use in the design.

```html
<!DOCTYPE html>
<html lang="en">
<head>
<meta charset="utf-8">
<title>RKP Advisory — Business Card</title>
<link rel="stylesheet" href="https://fonts.googleapis.com/css2?family=Playfair+Display:wght@400;700&family=Tinos:wght@400;700&family=Montserrat:wght@300;400&display=swap">
<style>
  :root {
    --stage: #2b2d30;
    --paper: #ffffff;
    --ink: #0b0b0b;
    --rule: #6a6a6a;
    --muted: #3a3a3a;
    --card-dark: #141414;
  }
  * { margin: 0; padding: 0; box-sizing: border-box; }
  html, body { width: 1200px; height: 900px; overflow: hidden; }
  body {
    background: var(--stage);
    position: relative;
    font-family: "Montserrat", sans-serif;
  }
  .card {
    position: absolute;
    left: 280px;
    width: 640px;
    height: 366px;
    overflow: hidden;
  }
  .card--contact { top: 60px; background: var(--paper); color: var(--ink); }
  .card--brand { top: 474px; background: var(--card-dark); }

  .accent-bar { position: absolute; background: var(--ink); }
  .accent-bar--left { left: 0; top: 0; width: 22px; height: 150px; }
  .accent-bar--right-upper { right: 0; top: 196px; width: 34px; height: 40px; }
  .accent-bar--right-lower { right: 0; top: 236px; width: 96px; height: 130px; }

  .company {
    position: absolute;
    left: 62px;
    top: 118px;
    width: 220px;
    text-align: left;
  }
  .company__name {
    font-family: "Playfair Display", serif;
    font-weight: 400;
    font-size: 31px;
    line-height: 1;
    color: var(--muted);
  }
  .company__tagline {
    margin-top: 8px;
    font-family: "Tinos", serif;
    font-size: 11px;
    letter-spacing: 0.6px;
    color: var(--ink);
  }
  .divider {
    position: absolute;
    left: 290px;
    top: 108px;
    width: 1px;
    height: 150px;
    background: var(--rule);
  }
  .contact {
    position: absolute;
    left: 312px;
    top: 110px;
  }
  .contact__name {
    font-family: "Tinos", serif;
    font-weight: 700;
    font-size: 22px;
    line-height: 1.1;
  }
  .contact__title {
    font-size: 13px;
    font-weight: 300;
    margin-top: 4px;
    color: var(--muted);
  }
  .contact__list { list-style: none; margin-top: 14px; }
  .contact__item {
    display: flex;
    align-items: center;
    gap: 8px;
    font-size: 13px;
    font-weight: 400;
    line-height: 1;
    margin-bottom: 10px;
  }
  .contact__icon { width: 12px; height: 12px; flex: none; }

  .brand-name {
    position: absolute;
    inset: 0;
    display: flex;
    align-items: center;
    justify-content: center;
    font-family: "Playfair Display", serif;
    font-weight: 400;
    font-size: 54px;
    color: var(--paper);
  }
</style>
</head>
<body>
  <section class="card card--contact">
    <div class="accent-bar accent-bar--left"></div>
    <div class="accent-bar accent-bar--right-upper"></div>
    <div class="accent-bar accent-bar--right-lower"></div>

    <div class="company">
      <p class="company__name">RKP Advisory</p>
      <p class="company__tagline">VIRTUAL ASSISTANCE</p>
    </div>

    <div class="divider"></div>

    <div class="contact">
      <p class="contact__name">Melissa Thornbury</p>
      <p class="contact__title">Owner/CEO</p>
      <ul class="contact__list">
        <li class="contact__item">
          <svg class="contact__icon" viewBox="0 0 12 12"><circle cx="6" cy="6" r="6" fill="#0b0b0b"/><path d="M3.8 3.2l1.1 1.3-.6.8c.5 1 1.3 1.8 2.3 2.3l.8-.6 1.3 1.1-.7 1c-2.6-.5-4.6-2.5-5.1-5.1z" fill="#fff"/></svg>
          555.302.9817
        </li>
        <li class="contact__item">
          <svg class="contact__icon" viewBox="0 0 12 12"><rect x="0.5" y="2" width="11" height="8" fill="#0b0b0b"/><path d="M1 2.6l5 3.6 5-3.6" stroke="#fff" stroke-width="0.9" fill="none"/></svg>
          info@rkpadvisory.net
        </li>
        <li class="contact__item">
          <svg class="contact__icon" viewBox="0 0 12 12"><circle cx="6" cy="6" r="5.5" fill="#0b0b0b"/><path d="M0.8 6h10.4M6 0.8c-2 2.8-2 7.6 0 10.4M6 0.8c2 2.8 2 7.6 0 10.4" stroke="#fff" stroke-width="0.8" fill="none"/></svg>
          www.rkpadvisory.net
        </li>
      </ul>
    </div>
  </section>

  <section class="card card--brand">
    <p class="brand-name">RKP Advisory</p>
  </section>
</body>
</html>
```